Rig up a website for a Rigging Company

We already have a logo. Looking for a website design that works on pavlune.com.
Our rigging company uses semi trucks, forklifts, and similar equipment to move large machines.
Our logo is white, black and red.

Target Market(s)

Medical Industry (moving medical equipment), Utility Industry (power equipment), Food Industry (moving bottling/packing equipment), US Government (large equipment)

Industry/Entity Type

It Company

Coding

Coded - Design and coding required

Number of Pages Required

5+ page

Font styles to use
Sans Serif

Colors
ec1f27
ffffff
0355a3

Requirements
Must have
• Home page, About page, Services Page, and Contact Information page
Nice to have
• Pictures of semi and forklifts and ability to insert our own pictures of our equipment

```html
<!DOCTYPE html>
<html lang="en">
<head>
<meta charset="utf-8">
<title>Halden Rigging</title>
<link href="https://fonts.googleapis.com/css2?family=Lato:wght@400;700&family=Open+Sans:wght@400;600;700&display=swap" rel="stylesheet">
<style>
:root{
  --red:#d0121b;
  --red-bright:#ec1f27;
  --ink:#222;
  --text:#555;
  --muted:#777;
  --light:#efefef;
  --footer:#232323;
  --footer-bottom:#141414;
  --white:#fff;
}
*{margin:0;padding:0;box-sizing:border-box}
html,body{width:1200px;height:2439px;overflow:hidden}
body{position:relative;font-family:"Open Sans",Arial,sans-serif;color:var(--text);background:var(--white)}
.abs{position:absolute}
.heading{font-family:"Lato",Arial,sans-serif}

/* header + hero */
.hero{left:0;top:0;width:1200px;height:650px;background:radial-gradient(ellipse at 50% 40%,#fafafa 0%,#ececec 70%,#e2e2e2 100%)}
.brand{left:117px;top:34px;font-family:"Lato",sans-serif;font-weight:700;font-size:38px;color:var(--ink);line-height:1}
.brand-sub{display:block;font-size:20px;letter-spacing:2px;margin-top:4px}
.nav{left:436px;top:0;display:flex;font-size:17px;color:#333;font-family:"Open Sans",sans-serif}
.nav a{color:inherit;text-decoration:none;position:absolute;top:41px;white-space:nowrap}
.nav a.active{color:var(--red)}
.nav a.active::before{content:"";position:absolute;left:-5px;right:-5px;top:-41px;height:4px;background:var(--red)}
.hero-title{left:111px;top:286px;font-size:36px;font-weight:700;line-height:47px;color:#1e1e1e;letter-spacing:.3px}
.hero-title span{color:var(--red)}
.hero-text{left:115px;top:386px;width:420px;font-size:14.5px;line-height:22px;color:#333}
.dots{left:115px;top:453px;display:flex;gap:8px}
.dots i{width:16px;height:16px;border-radius:50%;background:#111;display:block}
.dots i.on{background:#fff;border:2px solid #111}
.hero-photo{left:436px;top:122px;width:637px;height:463px;background:radial-gradient(ellipse at 55% 55%,#e6b83a 0%,#c99a25 18%,#4a4a4a 40%,rgba(80,80,80,.3) 65%,rgba(230,230,230,0) 80%)}

/* about */
.about{left:0;top:650px;width:1200px;height:410px;background:var(--white)}
.about-photo{left:0;top:0}
.about-title{left:112px;top:62px;font-size:34px;font-weight:400;color:#222}
.about-text{left:110px;top:125px;width:440px;font-size:14px;line-height:27px;color:#666}
.about-text p+p{margin-top:14px}
.btn-dark{left:110px;top:300px;width:137px;height:37px;background:linear-gradient(#666,#3c3c3c);border-radius:3px;color:#fff;font-size:13px;font-weight:700;display:flex;align-items:center;justify-content:center}

/* services */
.services{left:0;top:1060px;width:1200px;height:566px;background:linear-gradient(180deg,#3b3e4c 0%,#6a6470 45%,#8a6a5e 70%,#3a3333 100%)}
.services-title{left:0;top:45px;width:1200px;text-align:center;font-size:29px;font-weight:700;color:#fff;display:flex;justify-content:center;align-items:center;gap:20px}
.services-title::before,.services-title::after{content:"";width:38px;height:2px;background:#fff}
.card{top:111px;width:314px;height:392px}
.card-photo{width:314px;height:192px}
.card-body{height:200px;padding:22px 30px}
.card-title{font-size:25px;font-weight:400;margin-bottom:10px}
.card-text{font-size:12.5px;line-height:20px}
.card-btn{margin-top:20px;width:101px;height:34px;border:2px solid currentColor;font-size:13px;display:flex;align-items:center;justify-content:center}
.card-red .card-body{background:var(--red);color:#fff}
.card-black .card-body{background:#0c0c0c;color:#fff}
.card-white .card-body{background:#fff;color:var(--red)}
.card-white .card-text{color:#888}
.card-white .card-btn{color:var(--red)}
.card-white .card-title{color:var(--red)}

/* projects */
.projects-title{left:114px;top:1694px;font-size:26px;font-weight:700;color:#444}
.project-photo{top:1748px;width:235px;height:179px}
.project-body{top:1747px;width:220px}
.project-title{font-size:18px;color:#2b3a4a;font-family:"Open Sans",sans-serif;margin-bottom:14px}
.project-text{font-size:14px;line-height:22px;color:#666}
.project-more{margin-top:14px;font-size:14px;color:var(--red);font-weight:600}

/* footer */
.footer{left:0;top:2034px;width:1200px;height:334px;background:var(--footer);color:#ccc}
.foot-col{top:64px}
.foot-head{font-size:19px;color:#fff;font-family:"Lato",sans-serif;margin-bottom:12px;letter-spacing:.3px}
.foot-list{list-style:none;font-size:14px;line-height:24.5px}
.contact-line{display:flex;gap:12px;font-size:14px;line-height:22px;margin-bottom:8px}
.contact-line svg{flex:none;margin-top:4px}
.socials{display:flex;gap:10px;margin-top:22px}
.socials i{width:31px;height:31px;border-radius:50%;background:var(--red);display:block}
.foot-brand{left:810px;top:82px;font-family:"Lato",sans-serif;font-weight:700;font-size:44px;color:#fff;line-height:1}
.foot-brand span{display:block;font-size:24px;letter-spacing:3px;margin-top:4px}
.bottom{left:0;top:2368px;width:1200px;height:71px;background:var(--footer-bottom);color:#999;font-size:12px;display:flex;align-items:center;justify-content:center}
</style>
</head>
<body>

<section class="abs hero">
  <div class="abs brand">Halden<span class="brand-sub">RIGGING</span></div>
  <nav class="abs nav">
    <a class="active" style="left:0">HOME</a>
    <a style="left:86px">ABOUT US</a>
    <a style="left:203px">SERVICES</a>
    <a style="left:314px">EQUIPMENT</a>
    <a style="left:453px">PROJECT</a>
    <a style="left:570px">CONTACT</a>
  </nav>
  <h1 class="abs hero-title heading">FUSCE ULTRICIES ORCI AC<br><span>RIGGING SERVICES</span></h1>
  <p class="abs hero-text">Vivamus porttitor purus nisi eleifend libero a tempus libero lectus feugiat felis Morbi diam mauris viverra</p>
  <div class="abs dots"><i class="on"></i><i></i><i></i><i></i></div>
  <div class="abs hero-photo" role="img" aria-label="Yellow forklift with raised forks"></div>
</section>

<section class="abs about">
  <svg class="abs about-photo" width="1200" height="410" role="img" aria-label="Forklift on a loading site, tinted red">
    <defs>
      <linearGradient id="aboutRed" x1="0" y1="0" x2="1" y2="1">
        <stop offset="0" stop-color="#e21b22"/>
        <stop offset="1" stop-color="#a50d12"/>
      </linearGradient>
    </defs>
    <polygon points="683,0 1200,0 1200,410 525,410" fill="url(#aboutRed)"/>
  </svg>
  <h2 class="abs about-title heading">About Halden Rigging</h2>
  <div class="abs about-text">
    <p>Fusce ultricies orci ac feugiat suscipit leo massa sodales velit et scelerisque mi tortor at ipsum cligula augue</p>
    <p>bibendum accumsan vestibulum ut commodo a mi Morbi ornare gravida elit Integer congue augue et malesuada iaculis ipsum dui aliquet felis at cursus magna nisl nec elit Praesent</p>
  </div>
  <div class="abs btn-dark">READ MORE</div>
</section>

<section class="abs services" role="img" aria-label="Cranes against an evening sky">
  <h2 class="abs services-title heading">What We Do</h2>
  <article class="abs card card-red" style="left:111px">
    <div class="card-photo" style="background:linear-gradient(135deg,#c9d3de,#2a3550 55%,#6d6f72)" role="img" aria-label="Semi truck on a highway"></div>
    <div class="card-body"><h3 class="card-title heading">Semi Trucks</h3><p class="card-text">Donec dictum lectus non odio Cras a ante vitae enim iaculis aliquam Mauris nunc quam venenatis nec euismod</p><div class="card-btn">Read More</div></div>
  </article>
  <article class="abs card card-black" style="left:444px">
    <div class="card-photo" style="background:linear-gradient(135deg,#3a3a3a,#d9a52a 55%,#2a2a2a)" role="img" aria-label="Forklifts in a warehouse"></div>
    <div class="card-body"><h3 class="card-title heading">Forklifts</h3><p class="card-text">Donec dictum lectus non odio Cras a ante vitae enim iaculis aliquam Mauris nunc quam venenatis nec euismod</p><div class="card-btn">Read More</div></div>
  </article>
  <article class="abs card card-white" style="left:779px">
    <div class="card-photo" style="background:linear-gradient(160deg,#1d5fc4,#6fa8e8 55%,#e0b23a)" role="img" aria-label="Crane lifting a machine under blue sky"></div>
    <div class="card-body"><h3 class="card-title heading">Move Machines</h3><p class="card-text">Donec dictum lectus non odio Cras a ante vitae enim iaculis aliquam Mauris nunc quam venenatis nec euismod</p><div class="card-btn">Read More</div></div>
  </article>
</section>

<h2 class="abs projects-title heading">RECENT PROJECTS</h2>
<div class="abs project-photo" style="left:115px;background:linear-gradient(180deg,#6aa4d8,#d86a2a 60%,#2d5a7a)" role="img" aria-label="Offshore oil platform"></div>
<div class="abs project-body" style="left:372px">
  <h3 class="project-title">Project Tittle here</h3>
  <p class="project-text">tellus nec ultricies sit amet porttitor mattis enim In massa libero interdum nec interdum vel blandit sed nulla In ullamcorper est e</p>
  <p class="project-more">READ MORE</p>
</div>
<div class="abs project-photo" style="left:623px;background:linear-gradient(160deg,#2a4fb0,#c4c8cc 55%,#e0b03a)" role="img" aria-label="Crane truck at a job site"></div>
<div class="abs project-body" style="left:880px">
  <h3 class="project-title">Project Tittle here</h3>
  <p class="project-text">tellus nec ultricies sit amet porttitor mattis enim In massa libero interdum nec interdum vel blandit sed nulla In ullamcorper est e</p>
  <p class="project-more">READ MORE</p>
</div>

<footer class="abs footer">
  <div class="abs foot-col" style="left:115px">
    <h4 class="foot-head">COMPANY</h4>
    <ul class="foot-list"><li>Home</li><li>About Us</li><li>Why Us</li><li>Our Services</li><li>Our Team</li></ul>
  </div>
  <div class="abs foot-col" style="left:320px">
    <h4 class="foot-head">RESOURCES</h4>
    <ul class="foot-list"><li>Our Equipments</li><li>Our Projects</li><li>News</li><li>Blogs</li><li>Conact Us</li></ul>
  </div>
  <div class="abs foot-col" style="left:522px;width:260px">
    <h4 class="foot-head">CONTACT US</h4>
    <div class="contact-line"><svg width="12" height="16" viewBox="0 0 12 16"><path d="M6 0a6 6 0 0 0-6 6c0 4.5 6 10 6 10s6-5.5 6-10a6 6 0 0 0-6-6zm0 8.5A2.5 2.5 0 1 1 6 3.5a2.5 2.5 0 0 1 0 5z" fill="#fff"/></svg><span>412 Millbrook Lane Suite<br>210 Dalton, Georgia 30720</span></div>
    <div class="contact-line"><svg width="14" height="14" viewBox="0 0 14 14"><path d="M3 0l2.5 3.5-1.5 2a8 8 0 0 0 4.5 4.5l2-1.5L14 11l-2 3C5.5 14 0 8.5 0 2z" fill="#fff"/></svg><span>555-014-2236</span></div>
    <div class="contact-line"><svg width="14" height="14" viewBox="0 0 14 14"><rect x="1" y="4" width="12" height="9" rx="1" fill="#fff"/><rect x="3" y="0" width="8" height="5" fill="#fff"/><rect x="4" y="7" width="6" height="1.5" fill="#232323"/></svg><span>555-018-7741</span></div>
    <div class="socials"><i></i><i></i><i></i><i></i></div>
  </div>
  <div class="abs foot-brand">Halden<span>RIGGING</span></div>
</footer>
<div class="abs bottom">© 2017 Company Name &nbsp;All right reserved &nbsp;Term of Use</div>

</body>
</html>
```